Mastering Modern Vineyard Management

size of the ad - 8”x 10.75" plus 0.25" bleed
I would like an ad for a magazine that will stand out and make people want to read the ad.
The ad should not be crowded and people reading the ad will be able to read the text.
I would like it to be a creative and modern-day design.
the list of topics should not be the focus of the ad.
the text is attached.
If you decide to use people in the ad then please no ladies.
please note that leave over 1 inch for the bottom of the footer

```html
<!DOCTYPE html>
<html lang="en">
<head>
<meta charset="utf-8">
<title>Course Ad</title>
<link rel="stylesheet" href="https://fonts.googleapis.com/css2?family=Bebas+Neue&family=Poppins:wght@400;500;800&family=Open+Sans:wght@400&display=swap">
<style>
  :root {
    --ink: #000000;
    --panel: #1f1f1f;
    --red: #e4262d;
    --white: #ffffff;
    --frame-light: #f2f2f2;
    --frame-shade: #b9b9b9;
  }
  * { margin: 0; padding: 0; box-sizing: border-box; }
  html, body { width: 915px; height: 1200px; overflow: hidden; background: var(--ink); }
  .ad { position: relative; width: 915px; height: 1200px; background: var(--ink); font-family: "Poppins", sans-serif; color: var(--white); }
  .panel { position: absolute; left: 26px; top: 26px; width: 862px; height: 1042px; background: var(--panel); }
  .frame { position: absolute; background: linear-gradient(to bottom, var(--panel) 0%, #d6d6d6 38%, var(--frame-light) 75%, var(--frame-shade) 100%); }
  .photo { position: absolute; }
  .photo--tower { left: 41px; top: 81px; width: 166px; height: 254px; background: linear-gradient(160deg, #7fb6d6 0%, #8a6d5a 45%, #5c4538 100%); }
  .photo--estate { left: 270px; top: 62px; width: 314px; height: 292px; background: linear-gradient(180deg, #8a8aa8 0%, #6b6a78 35%, #c79a4a 65%, #3c3a34 100%); }
  .photo--campus { left: 655px; top: 81px; width: 166px; height: 254px; background: linear-gradient(180deg, #a8c8e6 0%, #5d86bf 45%, #8b9aa3 80%, #4d5a4a 100%); }
  .frame--left { left: 28px; top: 178px; width: 192px; height: 170px; }
  .frame--center { left: 255px; top: 178px; width: 344px; height: 185px; }
  .frame--right { left: 641px; top: 178px; width: 193px; height: 170px; }
  .center { position: absolute; left: 0; width: 915px; text-align: center; }
  .headline { top: 426px; font-family: "Bebas Neue", sans-serif; font-weight: 400; font-size: 99px; line-height: 1; }
  .subhead { top: 509px; font-weight: 800; font-size: 27px; line-height: 1; }
  .tagline { position: absolute; left: 137px; top: 546px; width: 641px; height: 31px; border-radius: 15px; background: var(--red); font-weight: 500; font-size: 16.5px; line-height: 31px; text-align: center; }
  .section-title { font-family: "Bebas Neue", sans-serif; font-weight: 400; color: var(--red); font-size: 58px; line-height: 1; }
  .location { top: 588px; }
  .details { top: 641px; font-size: 18px; line-height: 24.5px; }
  .offer { top: 726px; }
  .audience { top: 784px; font-size: 18px; line-height: 24px; }
  .topics-title { top: 820px; }
  .topics { position: absolute; top: 881px; width: 380px; list-style: none; text-align: center; font-size: 18px; line-height: 35px; }
  .topics--left { left: 45px; }
  .topics--right { left: 447px; }
  .divider { position: absolute; left: 428px; top: 890px; width: 1px; height: 155px; background: var(--red); }
  .free-space { position: absolute; left: 407px; top: 1091px; width: 100px; height: 66px; }
  .free-space__label { position: absolute; left: 0; top: 25px; width: 100px; text-align: center; font-family: "Open Sans", sans-serif; font-size: 11.5px; line-height: 16px; }
</style>
</head>
<body>
<main class="ad">
  <div class="panel">
    <div class="frame frame--left"></div>
    <div class="frame frame--center"></div>
    <div class="frame frame--right"></div>
    <div class="photo photo--tower" role="img" aria-label="Hillside vineyard rows under a blue sky"></div>
    <div class="photo photo--estate" role="img" aria-label="Modern winery estate lit at dusk"></div>
    <div class="photo photo--campus" role="img" aria-label="Vineyard estate with a landscaped walkway"></div>
  </div>

  <h1 class="center headline">VITICULTURE COURSE</h1>
  <h2 class="center subhead">MASTERING MODERN VINEYARD MANAGEMENT</h2>
  <p class="tagline">INVESTING IN KNOWLEDGE IS INVESTING IN OPPORTUNITIES.</p>

  <h3 class="center section-title location">GLENBROOK</h3>
  <p class="center details">10 -Tuesday evenings sessions<br>Starting Feb.28<br>Limited Partial Scholarships</p>

  <h3 class="center section-title offer">EARLY BIRD SPECIAL</h3>
  <p class="center audience">For those that started or would like to go into winegrowing</p>

  <h3 class="center section-title topics-title">TOPICS: PARTIAL LISTING</h3>
  <ul class="topics topics--left">
    <li>Financing</li>
    <li>Site selection</li>
    <li>Sourcing vines</li>
    <li>Canopy management</li>
    <li>Vineyard legal basics</li>
  </ul>
  <div class="divider"></div>
  <ul class="topics topics--right">
    <li>Pruning</li>
    <li>Pest control</li>
    <li>Tax fundamentals</li>
    <li>Dealing with wineries</li>
    <li>Vineyard investment strategies</li>
  </ul>

  <div class="free-space">
    <svg width="100" height="66" viewBox="0 0 100 66" aria-hidden="true">
      <line x1="50" y1="2" x2="50" y2="17" stroke="#fff" stroke-width="1"/>
      <polyline points="47,6 50,2 53,6" fill="none" stroke="#fff" stroke-width="1"/>
      <line x1="50" y1="47" x2="50" y2="63" stroke="#fff" stroke-width="1"/>
      <polyline points="47,59 50,63 53,59" fill="none" stroke="#fff" stroke-width="1"/>
    </svg>
    <span class="free-space__label">1 Inch Free</span>
  </div>
</main>
</body>
</html>
```